Meridian Tidewren Pale Ale Beer Label/Badge

We need a Beer Label designed for our first official beer to be launched under The meridian Brand!!
It will be a Pale Ale Called "Tidewren Pale Ale"!

The Meridian has the largest Craft Beer & Cider selection in the Geelong & Surf Coast region. With a funky location and a relaxed vibe, Meridian prides itself on serving delicious, unique seasonal food paired with Australia's best Craft Beer. The meridian is the perfect setting for a relaxed afternoon or evening with friends and can package an experience for larger groups or corporate bookings.

The Meridian Tavern brand has been growing for over a year and a half and the first label needs to integrate The meridian Logo but at the same time bring a fresh, new and eye catching feel to it along with embracing the "Odysseus" story in which we will be naming future beers.

The story of Tidewren is found via the following link
http://lorevault.example/wiki/Tidewren_(folklore)

We expect designers to research The meridian Tavern brand along with the all important Craft Beer Market and demographics. This will, potentially, be the start of many more labels to come for the winning designer!!

Requirements
Must have
• The original "O" needs to be integrated into the new logo and as much as the Greek mythology is being used it needs to be certain that this is an original Australian Craft Beer in the modern age!!
strong, modern & unique!!
Nice to have
• Logo could have a depiction of Tidewren
Should not have
• tackiness or cheap!!

```html
<!DOCTYPE html>
<html lang="en">
<head>
<meta charset="utf-8">
<title>Meridian Tidewren Pale Ale – Label</title>
<link rel="stylesheet" href="https://fonts.googleapis.com/css2?family=Bebas+Neue&family=Cinzel:wght@900&family=Josefin+Sans:wght@600&display=swap">
<style>
  :root {
    --page: #ffffff;
    --label-paper: #eeeae3;
    --band-dark: #8f2a1c;
    --ale-red: #d9261e;
    --ale-shadow: #6e1510;
    --wave-tan: #b98a73;
    --title-red: #a3171a;
    --brand-red: #8a2a22;
    --brand-brown: #3a1a12;
    --white: #ffffff;
  }
  html, body {
    margin: 0;
    width: 991px;
    height: 1200px;
    overflow: hidden;
    background: var(--page);
  }
  .beer-label {
    position: absolute;
    left: 152px;
    top: 50px;
    width: 686px;
    height: 1100px;
    background: var(--label-paper);
  }
  .beer-label svg { display: block; }
  .style-word { font-family: "Bebas Neue", "Arial Narrow", sans-serif; font-size: 168px; }
  .style-word--pale { fill: var(--white); }
  .style-word--ale { fill: var(--ale-red); }
  .style-word--ale-shadow { fill: var(--ale-shadow); }
  .beer-name { font-family: "Cinzel", serif; font-weight: 900; font-size: 112px; fill: var(--title-red); }
  .brand-name { font-family: "Bebas Neue", "Arial Narrow", sans-serif; font-size: 104px; fill: var(--brand-brown); letter-spacing: 6px; }
  .brand-tagline { font-family: "Josefin Sans", sans-serif; font-weight: 600; font-size: 28px; fill: var(--brand-brown); letter-spacing: 5px; }
</style>
</head>
<body>
  <main class="beer-label">
    <svg width="686" height="1100" viewBox="0 0 686 1100" xmlns="http://www.w3.org/2000/svg">
      <rect class="style-band" x="0" y="63" width="364" height="162" fill="var(--band-dark)"/>
      <text class="style-word style-word--pale" x="104" y="200" textLength="252" lengthAdjust="spacingAndGlyphs">PALE</text>
      <text class="style-word style-word--ale-shadow" x="398" y="204" textLength="198" lengthAdjust="spacingAndGlyphs">ALE</text>
      <text class="style-word style-word--ale" x="394" y="200" textLength="198" lengthAdjust="spacingAndGlyphs">ALE</text>

      <polygon class="wave-border wave-border--upper" role="img" aria-label="Greek wave mosaic border" points="0,369 686,245 686,377 0,493" fill="var(--wave-tan)" opacity="0.75"/>
      <polygon class="wave-border wave-border--lower" role="img" aria-label="Greek wave mosaic border" points="0,642 686,543 686,675 0,774" fill="var(--wave-tan)" opacity="0.75"/>

      <text class="beer-name" x="343" y="553" text-anchor="middle" textLength="540" lengthAdjust="spacingAndGlyphs" transform="rotate(-9 343 513)">TIDEWREN</text>

      <circle class="brand-dot" cx="343" cy="849" r="58" fill="var(--brand-red)"/>
      <text class="brand-name" x="343" y="1020" text-anchor="middle" textLength="430" lengthAdjust="spacingAndGlyphs">MERIDIAN</text>
      <text class="brand-tagline" x="343" y="1062" text-anchor="middle" textLength="413" lengthAdjust="spacingAndGlyphs">TAVERN + BREWERY</text>
    </svg>
  </main>
</body>
</html>
```